U.S. Popcorn company needs business cards

We are a popcorn company that manufactures popcorn and sells it to grocery stores worldwide. Our theme is "Americana" and our logo is U.S. route 66 which is the most famous highway in the U.S.

We would like the design to be simple and to use both sides. On the back side we would like to see just the logo and website. The front would be normal details

Target Market(s)

Wholesalers, grocers and distributors

Industry/Entity Type

Manufacture

Contact Information for Business Card

Business name: Prairie Lantern Popcorn
Phone: +1 555 308 4726
Email: Dale@prairielanternpopcorn.com
website: www.prairielanternpopcorn.com
Tag Line: "Kettle fresh, always"
Name: Dale Whitcombe
Title: Founder/President

Requirements
Must have
• Either this design should be fun or clean and simple. I will let you show me your thougths.
Nice to have
• Anything that ties in the real Hwy Route 66.
• Colors might need to be red, white and blue incorporated.
Should not have
• Not be too busy.

```html
<!DOCTYPE html>
<html lang="en">
<head>
<meta charset="utf-8">
<title>Prairie Lantern Popcorn – Business Cards</title>
<link href="https://fonts.googleapis.com/css2?family=Open+Sans:ital,wght@0,400;0,600;0,700;1,700&display=swap" rel="stylesheet">
<style>
  :root {
    --navy: #1f2e6e;
    --red: #e0262f;
    --white: #ffffff;
    --ray-pink: #f1dde2;
    --charcoal: #3b4147;
    --charcoal-light: #474d53;
    --backdrop: #ece9e4;
  }
  * { box-sizing: border-box; margin: 0; padding: 0; }
  html, body { width: 1200px; height: 950px; overflow: hidden; }
  body {
    background: var(--backdrop);
    font-family: "Open Sans", Arial, sans-serif;
    position: relative;
  }
  .card {
    position: absolute;
    top: 125px;
    width: 400px;
    height: 700px;
    overflow: hidden;
    box-shadow: 0 8px 24px rgba(0,0,0,0.18);
  }
  .card--front { left: 170px; background: var(--navy); }
  .card--back {
    left: 630px;
    background: radial-gradient(circle at 50% 45%, var(--charcoal-light), var(--charcoal));
    display: flex;
    align-items: center;
    justify-content: center;
  }
  .front-header { position: absolute; inset: 0; width: 400px; height: 700px; }
  .brand-name {
    font-weight: 700;
    color: var(--navy);
    text-align: center;
    line-height: 1.15;
  }
  .card--front .brand-name {
    position: absolute;
    top: 130px;
    left: 0;
    width: 100%;
    font-size: 30px;
  }
  .card--back .brand-name {
    color: var(--white);
    font-size: 32px;
  }
  .contact {
    position: absolute;
    top: 385px;
    left: 0;
    width: 100%;
    text-align: center;
    color: var(--white);
  }
  .contact__name {
    color: var(--red);
    font-size: 23px;
    font-weight: 600;
    text-transform: uppercase;
    letter-spacing: 0.5px;
  }
  .contact__title { font-size: 18px; margin-top: 2px; }
  .divider { font-size: 14px; letter-spacing: 3px; margin: 8px 0 6px; }
  .contact__line { font-size: 17px; line-height: 1.45; }
  .contact__line strong { font-weight: 700; }
  .tagline { font-size: 18px; font-weight: 700; font-style: italic; }
</style>
</head>
<body>
  <section class="card card--front" aria-label="Business card front">
    <svg class="front-header" viewBox="0 0 400 700">
      <defs>
        <radialGradient id="sunburst" cx="50%" cy="25%" r="75%">
          <stop offset="0" stop-color="#ffffff"/>
          <stop offset="1" stop-color="#f1dde2"/>
        </radialGradient>
      </defs>
      <path role="img" aria-label="Pale sunburst rays behind the company name"
            d="M0 0 H400 V215 C400 275 310 305 240 318 L200 352 L160 318 C90 305 0 275 0 215 Z"
            fill="url(#sunburst)"/>
      <path d="M0 215 C0 275 90 305 160 318 L200 352 L240 318 C310 305 400 275 400 215"
            fill="none" stroke="var(--red)" stroke-width="3"/>
    </svg>
    <p class="brand-name">Prairie Lantern<br>Popcorn</p>
    <div class="contact">
      <p class="contact__name">Dale Whitcombe</p>
      <p class="contact__title">Founder/President</p>
      <p class="divider">★★★</p>
      <p class="contact__line"><strong>Phone:</strong> +1 555 308 4726</p>
      <p class="contact__line">Dale@prairielanternpopcorn.com</p>
      <p class="contact__line">www.prairielanternpopcorn.com</p>
      <p class="divider">★★★</p>
      <p class="tagline">Kettle fresh, always</p>
    </div>
  </section>

  <section class="card card--back" aria-label="Business card back">
    <p class="brand-name">Prairie Lantern<br>Popcorn</p>
  </section>
</body>
</html>
```